PHGCCUL re-branding website and logo

We are looking for a new webpage design and logo our current page address is www.phgccul-example.org. We want to create a new design using PHGCCUL Pinewood and Harbour Growers Co-operative Credit Union limited and another with the purposed new name PHFC Pinewood and Harbour Financial Co-operative, the color scheme is purple and burnt orange. Our new logo and webpage should communicate change and growth purposed theme continuing our legacy here to server past, present and future generations. Our idea for the logo is a live shot of hands of different ages in a circle holding a tree

Target Market(s)

Everyone

Contact Information for Business Card

Company Name
Telephone number
Address
slot to enter employee info

Logo Text

(P & H) Pinewood And Harbour Financial Co-operative

Coding

Coded - Design and coding required

Number of Pages Required

2 page

Colors
f37122
fbed22
6b449b

Requirements
Must have
• links for social media

```html
<!DOCTYPE html>
<html lang="en">
<head>
<meta charset="utf-8">
<title>PHGCCUL – Home</title>
<link rel="stylesheet" href="https://fonts.googleapis.com/css2?family=Raleway:wght@300;400;500;600;700;800&display=swap">
<style>
:root{
  --purple:#6b449b;
  --orange:#e4521c;
  --peach:#fae4dc;
  --page:#ffffff;
  --muted:#7a5a9e;
}
*{box-sizing:border-box;margin:0;padding:0}
html,body{width:1007px;height:1200px;overflow:hidden;background:var(--page)}
body{position:relative;font-family:"Raleway",sans-serif;color:var(--purple)}
.abs{position:absolute}
.panel{position:absolute;background:var(--peach)}
a{color:inherit;text-decoration:none}

/* header */
.site-header{left:37px;top:0;width:949px;height:62px}
.brand{position:absolute;left:18px;top:17px;display:flex;align-items:center;gap:8px}
.brand-dot{width:22px;height:22px;border-radius:50%;background:var(--orange)}
.brand-name{font-size:22px;font-weight:700;color:var(--purple);letter-spacing:1px}
.brand-slash{position:absolute;left:178px;top:12px}
.main-nav a{position:absolute;top:22px;font-size:15px;color:var(--purple)}
.header-contact{position:absolute;left:789px;top:12px;font-size:14px;line-height:19px}

/* hero */
.hero{left:37px;top:77px;width:949px;height:344px;
  background:linear-gradient(100deg,#5d6470 0%,#9aa0a8 25%,#d7a98c 45%,#c9b7a8 60%,#6f6c6c 80%,#4e4c4e 100%)}
.hero-next{position:absolute;right:18px;top:160px}

/* quick links */
.quick-links{left:37px;top:435px;width:380px;height:263px}
.quick-title{position:absolute;left:44px;top:19px;font-size:19px;font-weight:700}
.quick-item{position:absolute;left:40px;display:flex;align-items:center;gap:12px;font-size:21px;font-weight:400}
.quick-icon{width:44px;height:44px;border-radius:50%;background:var(--purple);display:flex;align-items:center;justify-content:center}

/* mega menu */
.section-menu{left:446px;top:435px;width:540px;height:66px}
.section-menu .item{position:absolute;top:12px;font-size:16px;text-align:center}
.section-menu .caret{display:block;margin:6px auto 0}

/* notice */
.notice{left:446px;top:519px;width:540px;height:179px}
.notice-photo{position:absolute;left:0;top:0;width:221px;height:179px;
  background:linear-gradient(135deg,#3a3f45 0%,#8d939a 45%,#c7cbcf 70%,#9a8a80 100%)}
.notice-body{position:absolute;left:221px;top:0;width:319px;text-align:center}
.notice-title{margin-top:25px;font-size:19px;font-weight:500;line-height:22px}
.notice-text{margin-top:8px;font-size:12px;font-weight:400}
.notice-date{margin-top:9px;font-size:14px;font-weight:600}
.notice-btn{position:absolute;left:377px;top:129px;width:152px;height:26px;border:2px solid var(--purple);
  border-radius:9px;color:var(--orange);font-size:15px;font-weight:500;text-align:center;line-height:22px}

/* rates + news */
.rates-news{left:37px;top:719px;width:949px;height:304px}
.rates-title{position:absolute;left:25px;top:16px;font-size:17px;font-weight:500}
.rate{position:absolute;left:25px;width:323px}
.rate-name{font-size:14px;font-weight:500}
.rate-sub{font-size:11px;font-weight:400}
.rate-value{position:absolute;right:0;top:14px;font-size:11px}
.rates-note{position:absolute;left:25px;top:244px;font-size:12px}
.rates-note a{color:var(--orange)}
.news-title{position:absolute;left:380px;top:17px;width:569px;text-align:center;font-size:27px;font-weight:700}
.news-banner{position:absolute;left:380px;top:72px;width:560px;height:210px;border-radius:8px;
  background:linear-gradient(100deg,#1f3e6e 0%,#2f5a8e 45%,#7c8aa0 70%,#d9a868 100%)}
.news-banner span{position:absolute;left:29px;top:72px;font-size:42px;font-weight:500;color:#fff;letter-spacing:-1px}

/* footer */
.site-footer{left:37px;top:1044px;width:949px;height:119px}
.branch{position:absolute;top:15px;font-size:15px;line-height:18px}
.bottom-bar{left:37px;top:1176px;width:949px;height:15px;font-size:10px;line-height:15px}
.bottom-bar .copy{position:absolute;left:3px}
.bottom-bar .legal{position:absolute;right:28px}
</style>
</head>
<body>

<header class="panel site-header">
  <div class="brand"><span class="brand-dot"></span><span class="brand-name">PHGCCUL</span></div>
  <svg class="brand-slash" width="22" height="40" viewBox="0 0 22 40"><line x1="19" y1="1" x2="3" y2="39" stroke="#6b449b" stroke-width="2.5"/></svg>
  <nav class="main-nav">
    <a href="#" style="left:232px">HOME</a>
    <a href="#" style="left:313px">APPLY FOR A LOAN</a>
    <a href="#" style="left:484px">BECOME A MEMBER</a>
    <a href="#" style="left:664px">LOCATIONS</a>
  </nav>
  <div class="header-contact">Phone: (555) 014-2200<br>Fax: (555) 014-2291</div>
</header>

<section class="panel hero" role="img" aria-label="Photo of two business people shaking hands over a desk with a notebook">
  <svg class="hero-next" width="50" height="24" viewBox="0 0 50 24"><path d="M0 12H38M30 3l12 9-12 9" fill="none" stroke="#c9c9c9" stroke-width="5"/></svg>
</section>

<section class="panel quick-links">
  <div class="quick-title">INTERNET TELLER LOGIN</div>
  <a class="quick-item" href="#" style="top:67px"><span class="quick-icon"><svg width="24" height="14" viewBox="0 0 24 14"><path d="M0 7H18M13 1l7 6-7 6" fill="none" stroke="#fff" stroke-width="3"/></svg></span>APPLY FOR A LOAN</a>
  <a class="quick-item" href="#" style="top:135px"><span class="quick-icon"><svg width="24" height="14" viewBox="0 0 24 14"><path d="M0 7H18M13 1l7 6-7 6" fill="none" stroke="#fff" stroke-width="3"/></svg></span>BECOME A MEMBER</a>
  <a class="quick-item" href="#" style="top:203px"><span class="quick-icon"><svg width="24" height="14" viewBox="0 0 24 14"><path d="M0 7H18M13 1l7 6-7 6" fill="none" stroke="#fff" stroke-width="3"/></svg></span>FINANCIAL CALCULATORS</a>
</section>

<nav class="panel section-menu">
  <div class="item" style="left:19px">MY CREDIT UNION<svg class="caret" width="14" height="9"><path d="M0 0h14L7 9z" fill="#6b449b"/></svg></div>
  <div class="item" style="left:180px">PRODUCTS &amp; SERVICES<svg class="caret" width="14" height="9"><path d="M0 0h14L7 9z" fill="#6b449b"/></svg></div>
  <div class="item" style="left:378px">TOOLS &amp; BENEFITS<svg class="caret" width="14" height="9"><path d="M0 0h14L7 9z" fill="#6b449b"/></svg></div>
</nav>

<section class="panel notice">
  <div class="notice-photo" role="img" aria-label="Photo of a finger pressing an ATM keypad"></div>
  <div class="notice-body">
    <div class="notice-title">ATM CARDS<br>RENEWAL NOTICE</div>
    <div class="notice-text">Please be advised that all ATM cards issued feb 2014</div>
    <div class="notice-date">EXPIRES EFFECTIVE FEBRUARY 28, 2017</div>
  </div>
  <a class="notice-btn" href="#">LEARN MORE HERE</a>
</section>

<section class="panel rates-news">
  <div class="rates-title">FEATURED RATES</div>
  <div class="rate" style="top:58px"><div class="rate-name">CONSUMER LOANS</div><div class="rate-sub">as low as</div><div class="rate-value">9.00% APR*</div></div>
  <div class="rate" style="top:104px"><div class="rate-name">NEW AUTO/MOTORCYCLE</div><div class="rate-sub">as low as</div><div class="rate-value">7.00% APR*</div></div>
  <div class="rate" style="top:151px"><div class="rate-name">USED AUTO/MOTORCYCLE</div><div class="rate-sub">as low as</div><div class="rate-value">11.75% APR*</div></div>
  <div class="rate" style="top:198px"><div class="rate-name">MORTGAGES</div><div class="rate-sub">as low as</div><div class="rate-value">8.25% APR*</div></div>
  <div class="rates-note">*APR - Annual Percentage Rate. <a href="#">Apply For A Loan &gt;</a></div>
  <div class="news-title">NEWS AND EVENTS</div>
  <div class="news-banner" role="img" aria-label="Photo of a weekly planner notebook with ring binding"><span>News And Events</span></div>
</section>

<footer class="panel site-footer">
  <div class="branch" style="left:4px">NASSAU<br>LOCATION: Harbour Row &amp; Cedar Dr.<br>PHONE:&nbsp; (555) 014-2200<br>FAX: (555) 014-2291</div>
  <div class="branch" style="left:319px">FREEPORT, GRAND BAHAMA<br>LOCATION: #12 Pinecrest Ave.<br>Phone: (555) 017-3189<br>Fax: (555) 017-3036</div>
  <div class="branch" style="left:589px;top:8px">Abaco<br>Location: Willow Bay Market Plaza<br>Phone: (555) 019-4613<br>Fax: (555) 019-4612<br><span style="display:block;margin-top:6px">Island Co-operative Alliance Limited (ICAL).</span></div>
</footer>

<div class="panel bottom-bar">
  <span class="copy">Copyright © 2017 Pinewood &amp; Harbour Growers Co-operative Credit Union Ltd. All Rights Reserved.</span>
  <span class="legal">Privacy Policy Website Terms USA Patriot Act</span>
</div>

</body>
</html>
```